Ductless Mini Split Business Website

Copper Fern Services is looking to design an eye catching educational website about installing Ductless mini splits.

Similar to this company.
https://www.halvikstream.com/

Coding

Coded - Design and coding required

```html
<!DOCTYPE html>
<html lang="en">
<head>
<meta charset="utf-8">
<title>Copper Fern Services – Ductless Experts</title>
<link href="https://fonts.googleapis.com/css2?family=Signika:wght@400;600;700&family=Lato:wght@400;700&display=swap" rel="stylesheet">
<style>
:root{
  --yellow:#fdd20e;
  --yellow-deep:#f5c400;
  --ink:#1c1c22;
  --text:#3a3a3a;
  --muted:#8a8a8a;
  --gray-bg:#f2f2f2;
  --dark:#1d1e27;
  --dark-2:#15161d;
  --cyan:#1f8fc6;
  --navy:#22388e;
  --white:#ffffff;
  --head:"Signika",sans-serif;
  --body:"Lato",sans-serif;
}
*{box-sizing:border-box;margin:0;padding:0}
html,body{width:1200px;height:4648px;overflow:hidden}
body{position:relative;background:var(--white);font-family:var(--body);color:var(--text)}
.abs{position:absolute}
.heading{font-family:var(--head);font-weight:700;color:var(--ink);text-transform:uppercase}
.heading span{color:var(--yellow-deep)}
.btn{position:absolute;display:flex;align-items:center;justify-content:center;border-radius:30px;font-family:var(--head);font-weight:600;font-size:15px;text-transform:uppercase}
.btn-yellow{background:var(--yellow);color:var(--ink)}
.btn-ghost{border:2px solid var(--white);color:var(--white)}
.ph{position:absolute}

/* header */
.site-header{position:absolute;left:0;top:0;width:1200px;height:115px;background:var(--white);border-top:4px solid var(--dark)}
.brand{position:absolute;left:108px;top:18px;display:flex;align-items:center;gap:10px}
.brand-dot{width:30px;height:30px;border-radius:50%;background:var(--yellow)}
.brand-name{font-family:var(--head);font-weight:700;font-size:22px;color:var(--ink);line-height:1}
.brand-tag{position:absolute;left:110px;top:74px;font-family:var(--head);font-weight:700;font-size:17px;color:var(--ink);letter-spacing:.5px}
.call{position:absolute;left:722px;top:12px}
.call-icon{position:absolute;left:0;top:0;width:46px;height:46px;border-radius:50%;background:var(--yellow)}
.call-lines{position:absolute;left:66px;top:6px;font-size:13px;color:var(--text);line-height:22px;white-space:nowrap}
.call-number{position:absolute;left:171px;top:10px;font-family:var(--head);font-weight:700;font-size:25px;color:var(--ink);white-space:nowrap}
.nav{position:absolute;top:60px;left:0;height:55px}
.nav a{position:absolute;top:0;height:55px;display:flex;align-items:center;font-size:13px;color:var(--text);text-decoration:none;white-space:nowrap}
.nav a.active{background:#fde98a;border-top:3px solid var(--yellow-deep);padding:0 11px}

/* hero */
.hero{position:absolute;left:0;top:115px;width:1200px;height:607px;clip-path:polygon(0 0,100% 0,100% 517px,0 607px);background:linear-gradient(100deg,#cfc7bd 0%,#bfb4a8 35%,#c9bcb0 60%,#b8a89b 100%)}
.hero-title{position:absolute;left:660px;top:182px;font-family:var(--head);font-weight:600;font-size:20px;color:var(--ink)}
.badge{position:absolute;width:152px;height:152px;border-radius:50%;border:5px solid var(--white);display:flex;flex-direction:column;align-items:center;justify-content:flex-end;padding-bottom:28px;text-align:center;font-family:var(--head);font-weight:600;font-size:14px;line-height:20px;color:var(--white)}
.badge svg{margin-bottom:10px}
.badge-cyan{background:var(--cyan)}
.badge-yellow{background:var(--yellow);color:var(--ink)}
.badge-navy{background:var(--navy)}
.hero-sub{position:absolute;left:650px;top:442px;width:380px;text-align:center;font-family:var(--head);font-weight:600;font-size:17px;line-height:28px;color:var(--ink)}
.mascot{position:absolute;left:960px;top:652px;width:226px;height:166px;border-radius:50%;background:radial-gradient(circle at 45% 50%,#f4d33a,#e0b400 60%,rgba(255,255,255,0) 72%)}

/* about */
.about-photo{position:absolute;left:105px;top:748px;width:458px;height:454px;border-radius:50%;border-left:8px solid var(--yellow);border-bottom:8px solid var(--yellow);background:linear-gradient(160deg,#e9e6e2,#cfc9c2 60%,#a8a39d)}
.about-title{position:absolute;left:601px;top:834px;font-size:39px;white-space:nowrap}
.about-copy{position:absolute;left:599px;top:888px;width:490px;font-size:13px;line-height:26px;color:var(--muted);text-align:justify}

/* services */
.services-bg{position:absolute;left:0;top:1263px;width:1200px;height:1075px;background:var(--gray-bg)}
.services-title{position:absolute;left:0;width:1200px;top:1366px;text-align:center;font-size:38px}
.card{position:absolute;width:305px;height:336px;background:var(--white);box-shadow:0 2px 8px rgba(0,0,0,.08)}
.card .ph{left:16px;top:16px;width:273px;height:236px}
.card h3{position:absolute;left:0;top:266px;width:100%;text-align:center;font-family:var(--head);font-weight:600;font-size:18px;line-height:26px;color:var(--ink);text-transform:uppercase}
.card .view{position:absolute;left:0;top:120px;width:100%;text-align:center;font-size:13px;font-weight:700;color:var(--yellow);text-decoration:underline}

/* why */
.why-title{position:absolute;left:135px;top:2408px;font-size:39px;line-height:44px;white-space:nowrap}
.why-line{position:absolute;left:169px;top:2580px;width:2px;height:240px;background:var(--yellow)}
.why-icon{position:absolute;left:127px;width:86px;height:86px;border-radius:50%;background:var(--yellow);display:flex;align-items:center;justify-content:center}
.why-item h4{position:absolute;left:227px;font-family:var(--body);font-weight:400;font-size:21px;color:var(--ink)}
.why-item p{position:absolute;left:227px;width:285px;font-size:12px;line-height:21px;color:var(--muted)}
.why-photo{position:absolute;left:631px;top:2454px;width:454px;height:454px;border-radius:50%;border-right:9px solid var(--yellow);border-bottom:9px solid var(--yellow);background:linear-gradient(150deg,#d9dadb,#9fa4a8 55%,#6e7379)}
.tools{position:absolute;left:572px;top:2510px;width:100px;height:350px;background:linear-gradient(180deg,#c8c9cc,#9c9ea3 70%,#d9a43a);border-radius:10px;opacity:.7}

/* testimonials */
.testimonials{position:absolute;left:0;top:2984px;width:1200px;height:512px;clip-path:polygon(0 20px,100% 0,100% 480px,0 512px);background:linear-gradient(180deg,var(--dark) 0%,#23242f 50%,var(--dark-2) 100%)}
.t-title{position:absolute;left:0;width:1200px;top:3072px;text-align:center;font-size:33px;color:var(--white)}
.t-rule{position:absolute;left:578px;top:3122px;width:44px;height:3px;background:var(--yellow)}
.quote{position:absolute;width:285px;padding-left:24px;border-left:3px solid var(--yellow);font-size:13px;line-height:28px;color:#e5e5e5}
.person{position:absolute}
.person .q{position:absolute;left:0;top:0;width:38px;height:38px;border-radius:50%;background:var(--white);display:flex;align-items:center;justify-content:center}
.person .n{position:absolute;left:65px;top:-10px;font-family:var(--head);font-weight:700;font-size:14px;color:var(--white);white-space:nowrap}
.person .r{position:absolute;left:65px;top:24px;font-size:13px;color:#d5d5d5}
.dots{position:absolute;left:563px;top:3393px;display:flex;gap:6px}
.dots i{display:block;width:11px;height:11px;border-radius:50%;background:#d9d9d9}
.dots i:first-child{background:var(--yellow)}

/* contact */
.c-title{position:absolute;left:0;width:1200px;top:3530px;text-align:center;font-size:33px}
.c-intro{position:absolute;left:270px;top:3588px;width:660px;text-align:center;font-size:13px;line-height:25px;color:var(--muted)}
.map{position:absolute;left:0;top:3835px;width:1200px;height:403px;background:linear-gradient(120deg,#e4e2d6,#efeee7 45%,#dfe3d2 70%,#cfdbe6)}
.form-card{position:absolute;left:168px;top:3664px;width:857px;height:334px;background:var(--white);box-shadow:0 3px 14px rgba(0,0,0,.12)}
.info{position:absolute;left:0;top:0;width:359px;height:334px;background:#f4f4f4}
.info h5{position:absolute;left:37px;top:34px;font-family:var(--head);font-weight:600;font-size:15px;color:#555}
.info-row{position:absolute;left:75px;font-size:11px;line-height:18px;color:var(--muted)}
.info-ico{position:absolute;left:-32px;top:0}
.field{position:absolute;left:401px;width:418px;border-bottom:1px solid #d9d9d9;font-size:10px;color:#9a9a9a;padding-bottom:9px}
.robot{position:absolute;left:401px;top:245px;width:158px;height:40px;border:1px solid #d4d4d4;background:#f9f9f9;border-radius:3px;font-size:8px;color:#555;display:flex;align-items:center;gap:8px;padding-left:8px}
.robot b{display:block;width:14px;height:14px;border:2px solid #c1c1c1;background:var(--white)}
.robot i{position:absolute;right:8px;top:8px;width:22px;height:22px;background:#c9d3e8;border-radius:3px}
.pin-note{position:absolute;left:605px;top:4025px;width:274px;height:58px;background:var(--white);box-shadow:0 2px 6px rgba(0,0,0,.12);font-size:10px;line-height:18px;color:#777;padding:8px 10px 0 36px}

/* footer */
.footer{position:absolute;left:0;top:4238px;width:1200px;height:410px;background:var(--dark)}
.f-brand{position:absolute;left:112px;top:68px;display:flex;align-items:center;gap:10px}
.f-brand .brand-name{color:var(--yellow);font-size:24px}
.f-tag{position:absolute;left:114px;top:134px;font-family:var(--head);font-weight:600;font-size:22px;color:var(--yellow);letter-spacing:1px}
.social{position:absolute;top:189px;width:36px;height:36px;border-radius:50%;background:#5c5d66}
.social.on{background:var(--yellow)}
.f-head{position:absolute;top:77px;font-family:var(--head);font-weight:600;font-size:19px;color:var(--white);text-transform:uppercase}
.f-links{position:absolute;left:480px;top:117px;list-style:none}
.f-links li{font-size:13px;line-height:28.3px;color:#e8e8e8}
.f-links li::before{content:"»";margin-right:9px;color:var(--white)}
.f-copy{position:absolute;left:742px;top:116px;width:350px;font-size:13px;line-height:28px;color:#e8e8e8}
.f-input{position:absolute;left:748px;top:205px;width:338px;border-bottom:1px solid #9a9a9a;font-size:11px;color:#c8c8c8;padding:0 4px 10px}
.copyright{position:absolute;left:0;top:347px;width:1200px;height:63px;border-top:1px solid #3a3b45;text-align:center;line-height:60px;font-size:13px;color:#e8e8e8}
</style>
</head>
<body>

<header class="site-header">
  <div class="brand"><span class="brand-dot"></span><span class="brand-name">Copper Fern Services</span></div>
  <div class="brand-tag">DUCTLESS EXPERTS</div>
  <div class="call">
    <div class="call-icon">
      <svg width="46" height="46" viewBox="0 0 46 46"><path d="M17 14c2 0 3 4 3 5s-2 2-2 3c1 3 3 5 6 6 1 0 2-2 3-2s5 1 5 3-2 4-4 4c-8 0-15-7-15-15 0-2 2-4 4-4z" fill="#fff"/></svg>
    </div>
    <div class="call-lines">Call us Today :<br>( Need to Help )</div>
    <div class="call-number">+1 555 014 7720</div>
  </div>
  <nav class="nav">
    <a class="active" style="left:455px">Home</a>
    <a style="left:547px">About us</a>
    <a style="left:648px">FAQ</a>
    <a style="left:720px">Services</a>
    <a style="left:818px">Financing</a>
    <a style="left:924px">Reviews</a>
    <a style="left:1021px">Contact us</a>
  </nav>
</header>

<section class="hero" role="img" aria-label="Couple on a grey sofa enjoying cool air from a wall-mounted ductless unit in a brick-walled living room"></section>
<div class="hero-title">We Stand Behind Our Ductless Services</div>
<div class="badge badge-cyan" style="left:610px;top:249px">
  <svg width="40" height="52" viewBox="0 0 40 52"><path d="M8 14a12 12 0 1 1 18 10c-4 2-6 4-6 9" stroke="#fff" stroke-width="7" fill="none" stroke-linecap="round"/><circle cx="20" cy="46" r="4.5" fill="#fff"/></svg>
  Get Some<br>Answers</div>
<div class="badge badge-yellow" style="left:763px;top:249px">
  <svg width="40" height="52" viewBox="0 0 40 52"><path d="M14 4h12l-4 8h-4zM18 12c-12 6-16 16-14 26 2 8 30 8 32 0 2-10-2-20-14-26z" fill="#1c1c22"/><text x="20" y="38" font-size="16" font-family="Signika" font-weight="700" fill="#fdd20e" text-anchor="middle">$</text></svg>
  Our Financing<br>Options</div>
<div class="badge badge-navy" style="left:916px;top:249px">
  <svg width="44" height="48" viewBox="0 0 44 48"><rect x="4" y="6" width="30" height="38" fill="none" stroke="#fff" stroke-width="3"/><path d="M12 30l18-22 5 4-18 22h-5z" fill="#fff"/><path d="M10 38h16" stroke="#fff" stroke-width="3"/></svg>
  Stay Up To<br>Date</div>
<div class="hero-sub">See Other Ways We Can Help with Your Ductless Systems</div>
<div class="btn btn-yellow" style="left:693px;top:530px;width:137px;height:46px">Get a Quate</div>
<div class="btn btn-ghost" style="left:845px;top:530px;width:144px;height:46px">Contact Us</div>
<div class="mascot" role="img" aria-label="Cartoon bee mascot holding a wrench"></div>

<div class="about-photo" role="img" aria-label="Man and woman relaxing on a sofa under a ductless air unit"></div>
<h2 class="heading about-title">About <span>Copper Fern Service</span></h2>
<p class="about-copy">Sed ut perspiciatis unde omnis iste natus error sit voluptatem accusantium doloremque laudantium, totam rem aperiam, eaque ipsa quae ab illo inventore veritatis et quasi architecto beatae vitae dicta sunt explicabo. Nemo enim ipsam voluptatem quia voluptas sit aspernatur aut odit aut fugit, sed quia consequuntur magni dolores eos qui ratione voluptatem sequi nesciunt. Neque porro quisquam est, qui dolorem ipsum quia dolor sit amet</p>
<div class="btn btn-yellow" style="left:597px;top:1066px;width:141px;height:45px;font-size:14px">Read More »</div>

<div class="services-bg"></div>
<svg class="abs" style="left:0;top:1263px" width="1200" height="1100" viewBox="0 0 1200 1100">
  <polygon points="866,0 1200,0 1200,50" fill="#fdd20e"/>
  <polygon points="0,1038 720,1062 0,1089" fill="#fdd20e"/>
</svg>
<h2 class="heading services-title">How Can We <span>Help You?</span></h2>

<div class="card" style="left:112px;top:1444px"><div class="ph" style="background:linear-gradient(180deg,#f6f6f6,#d7d7d7 60%,#9a9a9a)" role="img" aria-label="Close-up of a white wall-mounted air unit"></div><h3>Baseboard Heat<br>Replacement</h3></div>
<div class="card" style="left:446px;top:1444px"><div class="ph" style="background:linear-gradient(180deg,#e8ce45,#d9bf3e 60%,#b9a35a)" role="img" aria-label="Living room with indoor unit under a yellow overlay"><span class="view">VIEW DETAILS &gt;</span></div><h3>Ductless for Additions &amp;<br>Remodels</h3></div>
<div class="card" style="left:780px;top:1444px"><div class="ph" style="background:linear-gradient(160deg,#8f6d5a,#c9cfd5 50%,#6b8aa3)" role="img" aria-label="Technician holding refrigerant pressure gauges"></div><h3>Ductless Heat Pump<br>FAQ</h3></div>
<div class="card" style="left:112px;top:1816px"><div class="ph" style="background:linear-gradient(160deg,#e2e0dd,#b9b6b2 50%,#4167a7)" role="img" aria-label="Installer in blue overalls fitting a wall unit"></div><h3>Ductless<br>Installation</h3></div>
<div class="card" style="left:446px;top:1816px"><div class="ph" style="background:linear-gradient(160deg,#d6d8da,#a2a6aa 60%,#5c6770)" role="img" aria-label="Gloved hands servicing an open indoor unit"></div><h3>Ductless<br>Maintenance</h3></div>
<div class="card" style="left:780px;top:1816px"><div class="ph" style="background:linear-gradient(160deg,#dcdcdc,#a9a9a9 60%,#6d6d6d)" role="img" aria-label="Hands repairing the inside of an air unit"></div><h3>Ductless<br>Repairs</h3></div>
<div class="btn btn-yellow" style="left:464px;top:2186px;width:274px;height:60px">More Ductless Services</div>

<div class="tools" role="img" aria-label="Wrenches, screwdriver, drill bit and paintbrush arranged as decoration"></div>
<div class="why-photo" role="img" aria-label="Smiling technician in a blue cap giving a thumbs up beside an indoor unit"></div>
<svg class="abs" style="left:826px;top:2650px" width="50" height="56" viewBox="0 0 50 56"><polygon points="6,4 44,28 6,52" fill="none" stroke="#fdd20e" stroke-width="5" stroke-linejoin="round"/></svg>
<h2 class="heading why-title">Why Choose<br><span>Copper Fern Services?</span></h2>
<div class="why-line"></div>
<div class="why-item">
  <div class="why-icon" style="top:2520px"><svg width="28" height="36" viewBox="0 0 28 36"><rect x="2" y="2" width="24" height="32" rx="3" fill="#1c1c22"/><rect x="7" y="7" width="14" height="8" fill="#fdd20e"/><circle cx="14" cy="25" r="4" fill="#fdd20e"/></svg></div>
  <h4 style="top:2520px">Tempor incididunt</h4>
  <p style="top:2554px">Lorem ipsum dolor sit amet, consectetur adipi scing elit, sed do eiusmod dolor sit ametconse ctetur adipicing elit, sed do tempor.</p>
</div>
<div class="why-item">
  <div class="why-icon" style="top:2652px"><svg width="30" height="34" viewBox="0 0 30 34"><path d="M10 2h10l-3 6h-4zM15 8C4 12 1 22 3 28c2 5 22 5 24 0 2-6-1-16-12-20z" fill="#1c1c22"/><text x="15" y="28" font-size="13" font-family="Signika" font-weight="700" fill="#fdd20e" text-anchor="middle">$</text></svg></div>
  <h4 style="top:2652px">Tempor incididunt</h4>
  <p style="top:2686px">Lorem ipsum dolor sit amet, consectetur adipi scing elit, sed do eiusmod dolor sit amet.once ctetur adipicing elit, sed do tempor.</p>
</div>
<div class="why-item">
  <div class="why-icon" style="top:2787px"><svg width="36" height="30" viewBox="0 0 36 30"><circle cx="18" cy="8" r="6" fill="#1c1c22"/><circle cx="7" cy="11" r="4.5" fill="#1c1c22"/><circle cx="29" cy="11" r="4.5" fill="#1c1c22"/><path d="M8 28c0-8 4-12 10-12s10 4 10 12zM0 26c0-6 3-9 7-9s4 2 4 2l-2 7zM36 26c0-6-3-9-7-9s-4 2-4 2l2 7z" fill="#1c1c22"/></svg></div>
  <h4 style="top:2787px">Tempor incididunt</h4>
  <p style="top:2821px">Lorem ipsum dolor sit amet, consectetur adipi scing elit, sed do eiusmod dolor sit amet,onse ctetur adipicing elit, sed do tempor.</p>
</div>

<section class="testimonials" role="img" aria-label="Dark background photo of an indoor unit on a wall"></section>
<h2 class="heading t-title">Our Testimonials</h2>
<div class="t-rule"></div>
<p class="quote" style="left:112px;top:3177px">Lorem Ipsum is simply dummy text of the printing &amp; typesetttetting industry. Lorem scrambled it to type specimen book.</p>
<p class="quote" style="left:451px;top:3177px">Lorem Ipsum is simply dummy text of the printing &amp; typesetttetting industry. Lorem scrambled it to type specimen book.</p>
<p class="quote" style="left:794px;top:3177px">Lorem Ipsum is simply dummy text of the printing &amp; typesetttetting industry. Lorem scrambled it to type specimen book.</p>
<div class="person" style="left:135px;top:3296px"><div class="q"><svg width="20" height="16" viewBox="0 0 20 16"><path d="M0 16V9C0 4 3 1 7 0l1 2C5 3 4 5 4 7h4v9zM11 16V9c0-5 3-8 7-9l1 2c-3 1-4 3-4 5h4v9z" fill="#1d1e27"/></svg></div><div class="n">Marta Quill</div><div class="r">Customer</div></div>
<div class="person" style="left:476px;top:3296px"><div class="q"><svg width="20" height="16" viewBox="0 0 20 16"><path d="M0 16V9C0 4 3 1 7 0l1 2C5 3 4 5 4 7h4v9zM11 16V9c0-5 3-8 7-9l1 2c-3 1-4 3-4 5h4v9z" fill="#1d1e27"/></svg></div><div class="n">Doran Pike</div><div class="r">Customer</div></div>
<div class="person" style="left:818px;top:3296px"><div class="q"><svg width="20" height="16" viewBox="0 0 20 16"><path d="M0 16V9C0 4 3 1 7 0l1 2C5 3 4 5 4 7h4v9zM11 16V9c0-5 3-8 7-9l1 2c-3 1-4 3-4 5h4v9z" fill="#1d1e27"/></svg></div><div class="n">Lise Okafor</div><div class="r">Customer</div></div>
<div class="dots"><i></i><i></i><i></i><i></i><i></i></div>

<h2 class="heading c-title">Our <span>Contact Us</span></h2>
<p class="c-intro">Lorem ipsum dolor sit amet, consectetur adipiscing elit, sed do eiusmod tempor incididunt ut labore et dolore magna aliqua. Ut enim ad minim veniam, quis nostrud exercit</p>
<div class="map" role="img" aria-label="Road map of the western and central United States"></div>
<div class="pin-note">
  <svg class="abs" style="left:10px;top:12px" width="16" height="22" viewBox="0 0 16 22"><path d="M8 0a8 8 0 0 1 8 8c0 6-8 14-8 14S0 14 0 8a8 8 0 0 1 8-8z" fill="#e02b2b"/><circle cx="8" cy="8" r="3" fill="#fff"/></svg>
  Lorem ipsum dolor sit amet, consectetur adipiscing elit, sed do eiusmod</div>
<svg class="abs" style="left:612px;top:4102px" width="24" height="34" viewBox="0 0 24 34"><path d="M12 0a12 12 0 0 1 12 12c0 9-12 22-12 22S0 21 0 12A12 12 0 0 1 12 0z" fill="#6e6e6e"/><circle cx="12" cy="12" r="4.5" fill="#fff"/></svg>

<div class="form-card">
  <div class="info">
    <h5>CONTACT INFORMATION</h5>
    <div class="info-row" style="top:96px;width:210px"><svg class="info-ico" width="14" height="20" viewBox="0 0 14 20"><path d="M7 0a7 7 0 0 1 7 7c0 5-7 13-7 13S0 12 0 7a7 7 0 0 1 7-7z" fill="#444"/><circle cx="7" cy="7" r="2.5" fill="#f4f4f4"/></svg>Lorem ipsum dolor sit amet, consectetur adipiscing elit, sed do eiusmod tempor incididunt ut labore</div>
    <div class="info-row" style="top:181px"><svg class="info-ico" width="18" height="18" viewBox="0 0 18 18"><path d="M4 0c2 0 3 3 3 4s-2 2-2 2c1 3 3 5 6 6 0 0 1-2 2-2s4 1 4 3-2 3-3 3C6 16 0 10 0 3c0-1 2-3 4-3z" fill="#444"/></svg>+1 555 014 7720</div>
    <div class="info-row" style="top:235px"><svg class="info-ico" width="20" height="14" viewBox="0 0 20 14"><rect width="20" height="14" fill="#444"/><path d="M0 0l10 8 10-8" fill="none" stroke="#f4f4f4" stroke-width="1.5"/></svg>info@copperfernservices.com</div>
  </div>
  <div class="field" style="top:44px">👤 Your name*</div>
  <div class="field" style="top:92px">✉ Email Address*</div>
  <div class="field" style="top:138px">✆ Phone*</div>
  <div class="field" style="top:215px">✎ Message*</div>
  <div class="robot"><b></b>I'm not a robot<i></i></div>
  <div class="btn btn-yellow" style="left:678px;top:245px;width:140px;height:44px;font-size:15px">Submit</div>
</div>

<footer class="footer">
  <div class="f-brand"><span class="brand-dot"></span><span class="brand-name">Copper Fern Services</span></div>
  <div class="f-tag">DUCTLESS EXPERTS</div>
  <span class="social" style="left:116px"></span>
  <span class="social on" style="left:157px"></span>
  <span class="social" style="left:199px"></span>
  <span class="social" style="left:240px"></span>
  <div class="f-head" style="left:480px">Quick Links</div>
  <ul class="f-links">
    <li>Home</li><li>About us</li><li>FAQ</li><li>Services</li><li>Financing</li><li>Reviews</li><li>Contact us</li>
  </ul>
  <div class="f-head" style="left:736px">Sign Up for Newsletter</div>
  <p class="f-copy">Lorem ipsum dolor sit amet, consectetur adipiscing elit, sed do eiusmod tempor incididunt ut labore</p>
  <div class="f-input">✉ Email Address*</div>
  <div class="btn btn-yellow" style="left:744px;top:251px;width:124px;height:42px;font-size:15px">Subscribe</div>
  <div class="copyright">© Copyrights 2019 Copper Fern Services. | All rights Reserved</div>
</footer>

</body>
</html>
```